Request for Business Card Design

Hi. My name is Marlene, I am looking for a new business card design for my company, Quarrow Signal Instruments, LLC. I really like the design you did for Tarsel Venture and was hoping you could do something similar using our full logo and our mark. I am also open to any raised texture design using our mark. I have attached our full logo, which would need to be somewhere on the card, as well as the mark in both outline and full form, as well as our brand colors / guide. The card does not have to be white, as long as our logo and mark appear. I actually like darker colored business cards more, but am open to all options. If you are interested in working with me, please let me know. We would also take the business card design into letterhead design if you can do that.

```html
<!DOCTYPE html>
<html lang="en">
<head>
<meta charset="utf-8">
<title>Quarrow Signal Instruments – Business Card</title>
<link rel="stylesheet" href="https://fonts.googleapis.com/css2?family=Open+Sans:wght@400;600;700;800&display=swap">
<style>
  :root {
    --stage: #2a2a2c;
    --card: #151516;
    --card-deep: #0d0d0e;
    --accent: #1a9fc6;
    --ink: #ffffff;
    --ink-soft: #d9d9d9;
    --emboss: #1f1f21;
  }
  * { box-sizing: border-box; margin: 0; padding: 0; }
  html, body {
    width: 1200px; height: 900px; overflow: hidden;
    background: var(--stage);
    font-family: "Open Sans", Arial, sans-serif;
  }
  .sheet {
    width: 1200px; height: 900px;
    display: flex; flex-direction: column; align-items: center; justify-content: center;
    gap: 40px;
  }
  .card {
    position: relative;
    width: 700px; height: 400px;
    background: var(--card);
    overflow: hidden;
    box-shadow: 0 18px 40px rgba(0,0,0,.45);
  }
  /* front */
  .card--front { border-bottom: 4px solid var(--accent); }
  .brand {
    position: absolute; left: 160px; top: 44px;
    display: flex; align-items: center; gap: 16px;
  }
  .brand__dot { width: 46px; height: 46px; border-radius: 50%; background: var(--accent); }
  .brand__name {
    font-weight: 800; font-size: 40px; letter-spacing: 3px; color: var(--ink); line-height: 1;
  }
  .brand__tagline {
    position: absolute; left: 222px; top: 92px;
    font-size: 10.5px; font-weight: 600; letter-spacing: 1.2px; color: var(--ink);
  }
  .holder {
    position: absolute; left: 60px; top: 140px;
    padding-left: 24px;
  }
  .holder::before {
    content: ""; position: absolute; left: 0; top: 2px;
    width: 12px; height: 40px; background: var(--accent);
  }
  .holder__name {
    font-weight: 800; font-size: 26px; color: var(--accent); letter-spacing: .5px; line-height: 1.1;
  }
  .holder__role { font-size: 17px; color: var(--ink-soft); margin-top: 2px; }
  .address {
    position: absolute; left: 84px; top: 214px;
    font-size: 17px; line-height: 1.3; color: var(--ink);
  }
  .contacts {
    position: absolute; left: 62px; top: 276px;
    list-style: none; font-size: 17px; color: var(--ink); line-height: 1.4;
  }
  .contacts li { display: flex; align-items: center; gap: 10px; }
  .contacts svg { width: 14px; height: 14px; flex: none; }
  .mark-area {
    position: absolute; right: 40px; bottom: 30px;
    width: 280px; height: 260px; border-radius: 50% 50% 46% 46%;
    background: radial-gradient(circle at 50% 55%, #1e1e20 0%, var(--card-deep) 55%, var(--card) 75%);
  }
  /* back */
  .card--back {
    display: flex; align-items: center; justify-content: center;
  }
  .texture {
    position: absolute; inset: 0;
    background: linear-gradient(135deg, var(--emboss), var(--card-deep) 50%, var(--emboss));
  }
  .back-brand {
    position: relative;
    display: flex; align-items: center; gap: 14px;
  }
  .back-brand__dot { width: 40px; height: 40px; border-radius: 50%; background: var(--accent); }
  .back-brand__name { font-weight: 800; font-size: 34px; letter-spacing: 3px; color: var(--accent); }
</style>
</head>
<body>
<main class="sheet">
  <section class="card card--front">
    <div class="brand">
      <span class="brand__dot"></span>
      <span class="brand__name">QUARROW</span>
    </div>
    <div class="brand__tagline">SIGNAL INSTRUMENTS</div>

    <div class="holder">
      <h1 class="holder__name">DARIO PELL</h1>
      <p class="holder__role">Managing Director</p>
    </div>

    <p class="address">Your address, City<br>State, Zip 1234</p>

    <ul class="contacts">
      <li>
        <svg viewBox="0 0 16 16" aria-hidden="true"><path fill="#1a9fc6" d="M3.5 1.5l2.5 0 1 3.5-1.8 1.2a9 9 0 0 0 4.6 4.6L11 9l3.5 1v2.5c0 1-1 2-2 2A11 11 0 0 1 1.5 3.5c0-1 1-2 2-2z"/></svg>
        123 456 789
      </li>
      <li>
        <svg viewBox="0 0 16 16" aria-hidden="true"><rect x="1" y="3" width="14" height="10" fill="#1a9fc6"/><path d="M1 3l7 6 7-6" fill="none" stroke="#151516" stroke-width="1.4"/></svg>
        info@yourmail.com
      </li>
      <li>
        <svg viewBox="0 0 16 16" aria-hidden="true"><circle cx="8" cy="8" r="6.5" fill="none" stroke="#1a9fc6" stroke-width="1.5"/><path d="M1.5 8h13M8 1.5c-3 3.5-3 9.5 0 13M8 1.5c3 3.5 3 9.5 0 13" fill="none" stroke="#1a9fc6" stroke-width="1.2"/></svg>
        www.yourwebsite.com
      </li>
    </ul>

    <div class="mark-area" role="img" aria-label="Large tone-on-tone brand mark embossed in the card corner"></div>
  </section>

  <section class="card card--back">
    <div class="texture" role="img" aria-label="Raised tone-on-tone repeat of the brand mark across the card"></div>
    <div class="back-brand">
      <span class="back-brand__dot"></span>
      <span class="back-brand__name">QUARROW</span>
    </div>
  </section>
</main>
</body>
</html>
```